Professional Business Card - TWO SIDES

I need a new business card design to be used by myself and my employees. I would like a professional card and for the front I thought I would like a dark blue thatch with our logo in a raised gold foil on top of it. On the other side I would like name, position, and contact info. I've uploaded our old design for an example of the info used.

Target Market(s)

Business Clients

Industry/Entity Type

CPA Firm

Contact Information for Business Card

Logo, Name, Title, Address, Phone Numbers, Website address, Email Address

Font styles to use
Serif
Sans Serif

Colors
0054AA
0677BA
7BADD7
CADEEF
E8F1F8
0094D4
00A9DD
6FCCEA
C7EBF8
E9F6FB

Requirements
Must have
• Modern Professional Look
Nice to have
• Logo in Gold Foil or ability to have is raised. I like our logo in a single color
Should not have
• I've uploaded old business card

```html
<!DOCTYPE html>
<html lang="en">
<head>
<meta charset="utf-8">
<title>Bexley &amp; Bexley CPA – Business Card</title>
<link rel="stylesheet" href="https://fonts.googleapis.com/css2?family=Arimo:wght@400;700&display=swap">
<style>
  :root {
    --backdrop: #2a2a2b;
    --navy: #16365f;
    --gold: #c9a03a;
    --paper: #ffffff;
    --ink: #16365f;
    --ink-soft: #1e2a3a;
  }
  * { box-sizing: border-box; margin: 0; padding: 0; }
  html, body {
    width: 1200px; height: 900px; overflow: hidden;
    background: var(--backdrop);
    font-family: "Arimo", Arial, sans-serif;
  }
  .canvas {
    width: 1200px; height: 900px;
    display: flex; flex-direction: column; align-items: center; justify-content: center;
    gap: 24px;
  }
  .card {
    width: 700px; height: 400px; position: relative; overflow: hidden;
  }
  /* Front */
  .card--front {
    background: var(--navy);
    display: flex; align-items: center; justify-content: center;
  }
  .wordmark {
    color: var(--gold); font-weight: 700; text-align: center;
  }
  .wordmark__name {
    display: block; font-size: 54px; letter-spacing: 1px; line-height: 1;
  }
  .wordmark__descriptor {
    display: block; font-size: 17px; letter-spacing: 5px; margin-top: 12px;
  }
  /* Back */
  .card--back { background: var(--paper); }
  .card--back .wordmark {
    position: absolute; left: 44px; top: 40px; text-align: left; color: var(--ink);
  }
  .card--back .wordmark__name { font-size: 36px; }
  .card--back .wordmark__descriptor { font-size: 12px; letter-spacing: 3.4px; margin-top: 8px; }
  .holder {
    position: absolute; left: 0; top: 150px;
    padding-left: 44px; border-left: 0;
  }
  .holder__bar {
    position: absolute; left: 0; top: 2px; width: 18px; height: 50px; background: var(--navy);
  }
  .holder__name {
    color: var(--ink); font-weight: 700; font-size: 26px; letter-spacing: 0.5px;
  }
  .holder__role {
    color: var(--ink-soft); font-size: 18px; margin-top: 2px;
  }
  .contacts {
    position: absolute; left: 44px; top: 222px; list-style: none;
  }
  .contacts li {
    display: flex; align-items: center; gap: 10px;
    color: var(--ink-soft); font-size: 18px; line-height: 28px;
  }
  .contacts svg { width: 16px; height: 16px; fill: var(--ink); flex: none; }
  .address-band {
    position: absolute; left: 0; right: 0; top: 320px; height: 40px;
    background: var(--navy); color: var(--paper);
    font-size: 18px; line-height: 40px; padding-left: 44px;
  }
</style>
</head>
<body>
<main class="canvas">
  <section class="card card--front" aria-label="Card front">
    <div class="wordmark">
      <span class="wordmark__name">BEXLEY &amp; BEXLEY</span>
      <span class="wordmark__descriptor">CERTIFIED PUBLIC ACCOUNTANTS</span>
    </div>
  </section>

  <section class="card card--back" aria-label="Card back">
    <div class="wordmark">
      <span class="wordmark__name">BEXLEY &amp; BEXLEY</span>
      <span class="wordmark__descriptor">CERTIFIED PUBLIC ACCOUNTANTS</span>
    </div>

    <div class="holder">
      <span class="holder__bar"></span>
      <p class="holder__name">DANIEL REYES</p>
      <p class="holder__role">Founder</p>
    </div>

    <ul class="contacts">
      <li>
        <svg viewBox="0 0 16 16" aria-hidden="true"><path d="M1 6c0-2 3-4 7-4s7 2 7 4v1h-3.5V5.5h-7V7H1zM3 8h10l1.5 6h-13z"/></svg>
        (555) 014 2290
      </li>
      <li>
        <svg viewBox="0 0 16 16" aria-hidden="true"><path d="M1 3h14v10H1zM2.5 4.5v.4L8 9l5.5-4.1v-.4z"/></svg>
        info@bexleycpa.com
      </li>
      <li>
        <svg viewBox="0 0 16 16" aria-hidden="true"><path d="M8 1a7 7 0 1 0 0 14A7 7 0 0 0 8 1zm0 1.5a5.5 5.5 0 0 1 5.4 4.5H10.6A9 9 0 0 0 8.9 2.6 5.6 5.6 0 0 0 8 2.5zM2.6 9h2.8a9 9 0 0 0 1.7 4.4A5.5 5.5 0 0 1 2.6 9zm0-2a5.5 5.5 0 0 1 4.5-4.4A9 9 0 0 0 5.4 7zm4.3 0A7.5 7.5 0 0 1 8 3.4 7.5 7.5 0 0 1 9.1 7zm0 2h2.2A7.5 7.5 0 0 1 8 12.6 7.5 7.5 0 0 1 6.9 9zm2 4.4A9 9 0 0 0 10.6 9h2.8a5.5 5.5 0 0 1-4.5 4.4z"/></svg>
        www.bexleycpa.com
      </li>
    </ul>

    <p class="address-band">412 N. Harlow Street Country Name, AB 20418</p>
  </section>
</main>
</body>
</html>
```